ORV Fashion Design Company Needs a New Web Design, Please Click Me

Designers:

PLEASE NOTE: we only need the web page design, not a fully coded website.

Our brand's name is Orbel Vantra, our signature is print. our style is edgy and chic.

The old website is too messy. here's the address:
www.orvdesign.example.cn

The new website's purpose is to show our brand/design and most importantly, sell products, So it should be a combination of a designer official website and online shopping. I want the whole style to be clean, edgy and pioneer, easy to understand. we need a sophisticated online shopping website.

The reference websites are:
liromapek.example.uk
www.qd-besu.example
talemkorv.example
misolvare.example
pardelunitram.example

Please beat their designs :)

Check out our lasted fashion show to get to know us more.

https://www.videohost.example/watch?v=ZkrpLmWnaYd&spfreload=10

The attachments are our Logo and some 2015 Look Book.
(Please let us know if you want to play with our print in this particular web design, we can send the source file.)
Updates

Designers, we really like the design of helenamardoux.example(we have attached a picture of the website) , Can we get a homepage like that? so the designs you submit will be 3 pages. The first one should be a page that only has Shop/Look. then the shop page, it should be nothing but our product which we will list the categories ourself. And the look page should contain all the info. such as news, about us and designers etc. Thank you all for your hard work, we really enjoyed the designs. Added Monday, November 03, 2014

Target Market(s)

Our target audiences are woman aged from 16-40 who like online shopping

Industry/Entity Type

Online Shopping

Number of Pages Required

3 page

Font styles to use
Serif
Sans Serif
Script

Requirements
Must have
• Designers,
• we really like the design of helenamardoux.example(we have attached a picture of the website) , Can we get a homepage like that? so the designs you submit will be 3 pages. The first one should be a page that only has Shop/Look. then the shop page, it should be nothing but our product which we will list the categories ourself. And the look page should contain all the info. such as news, about us and designers etc. Thank you all for your hard work, we really enjoyed the designs.

```html
<!DOCTYPE html>
<html lang="en">
<head>
<meta charset="utf-8">
<title>Orbel Vantra — Online Shopping</title>
<link rel="stylesheet" href="https://fonts.googleapis.com/css2?family=Open+Sans:wght@400;600;700&family=Oswald:wght@300;400;500;600&family=Playfair+Display:ital@0;1&display=swap">
<style>
:root{
  --ink:#111;
  --text:#333;
  --muted:#888;
  --line:#dcdcdc;
  --band:#ececec;
  --footer:#efefef;
  --salmon:#f57d6c;
  --red:#d9483b;
  --coral-btn:#f06b5a;
  --blue:#3a95d8;
  --white:#fff;
}
*{box-sizing:border-box;margin:0;padding:0}
html,body{width:1200px;height:2899px;overflow:hidden}
body{position:relative;background:var(--white);font-family:"Open Sans",Arial,sans-serif;color:var(--text)}
.abs{position:absolute}
.topbar{top:0;left:0;width:1200px;height:29px;background:var(--ink);color:var(--white);font-size:11px;font-weight:600}
.topbar span{position:absolute;top:7px;white-space:nowrap}
.topbar .sep{top:0;width:1px;height:29px;background:#444}
.logo{top:40px;left:114px;width:162px;text-align:center}
.logo-mark{width:52px;height:52px;border-radius:50%;background:var(--red);margin:0 auto 4px}
.logo-name{font-family:"Playfair Display",serif;font-size:11px;line-height:12px;color:var(--ink);letter-spacing:1px}
.nav{top:72px;left:412px;display:flex;gap:20px;font-size:16px;color:var(--ink);white-space:nowrap}
.cart{top:52px;left:923px;width:162px;height:64px;border:1px solid var(--line);font-size:10px;color:var(--muted)}
.cart .label{position:absolute;top:8px;left:9px}
.cart .total{position:absolute;bottom:12px;right:10px}
.cart .bag{position:absolute;bottom:10px;left:10px;width:18px;height:14px;background:#bbb}
.hero{top:135px;left:0;width:1200px;height:441px;background:linear-gradient(90deg,#f2f0ec,#e9e6e1)}
.hero-photo{position:absolute;left:599px;top:0;width:601px;height:441px;
  background:
   linear-gradient(90deg,#ebe7e2 0%,rgba(235,231,226,0) 8%,rgba(235,231,226,0) 88%,#e8e4df 100%),
   linear-gradient(180deg,#f17c5f 0%,#ee7659 42%,#d8ac92 50%,#4f6d90 58%,#3e5a7c 78%,#d6b39b 88%,#e9e4de 100%)}
.hero-rule{top:570px;left:0;width:1200px;height:6px;background:#cfcfcf}
.hero-copy{top:172px;left:178px;width:362px;text-align:center}
.hero-kicker{font-family:"Playfair Display",serif;font-style:italic;font-size:30px;line-height:40px;color:#6b6b6b;display:flex;align-items:center;gap:14px;justify-content:center}
.hero-kicker i{display:block;width:72px;height:2px;background:#888}
.hero-title{font-family:"Oswald",sans-serif;font-weight:600;font-size:80px;line-height:76px;background:linear-gradient(90deg,#e58a8c,#dcb97a);-webkit-background-clip:text;background-clip:text;color:transparent}
.hero-bar{height:4px;background:#666;margin:6px 0 3px}
.hero-bar.thin{height:1px}
.hero-sub{font-family:"Oswald",sans-serif;font-weight:300;font-size:32px;line-height:40px;color:#444;margin-top:2px}
.btn-hero{top:438px;left:274px;width:155px;height:55px;background:var(--red);color:var(--white);font-size:15px;line-height:55px;text-align:center;box-shadow:0 3px 0 #9b2f26}
.slide-arrow{top:300px;width:30px;height:112px;background:var(--white);opacity:.9}
.slide-arrow svg{position:absolute;top:48px;left:9px}
.dots{top:605px;left:535px;display:flex;gap:20px}
.dots i{width:11px;height:11px;border-radius:50%;background:#999}
.dots i.on{background:var(--red)}
.newsband{top:651px;left:0;width:1200px;height:54px;background:var(--band);font-size:12px}
.newsband .t{position:absolute;top:18px}
.email{position:absolute;top:13px;left:193px;width:132px;height:29px;background:var(--white);font-size:11px;color:#aaa;padding:6px 8px}
.email-go{position:absolute;top:13px;left:325px;width:29px;height:29px;background:var(--red)}
.social-tab{position:absolute;top:0;width:55px;height:54px;border-left:1px solid #d4d4d4}
.social-tab i{position:absolute;top:17px;left:19px;width:18px;height:18px;border-radius:50%;background:#666}
.tile{position:absolute}
.tile-main{top:746px;left:114px;width:485px;height:340px;background:linear-gradient(90deg,#cfc9c2 0%,#3c3a3a 22%,#8a817a 34%,#d8d8d8 48%,#eeeeee 100%)}
.looks{position:absolute;left:255px;top:20px;width:210px;text-align:center;font-family:"Oswald",sans-serif}
.looks .a{font-size:36px;font-weight:600;color:#333;line-height:38px}
.looks .b{font-size:64px;font-weight:300;color:#333;line-height:66px}
.looks .c{display:inline-block;width:32px;height:32px;border-radius:50%;background:#333;color:var(--white);font-size:18px;line-height:32px}
.looks .d{font-size:76px;font-weight:600;color:var(--blue);line-height:78px}
.t1{top:746px;left:601px;width:240px;height:167px;background:linear-gradient(135deg,#163a52,#6f93ad 55%,#2e5670)}
.t2{top:746px;left:845px;width:241px;height:167px;background:radial-gradient(circle,#8fcbe3,#2a86b3 70%,#1d6b93)}
.t3{top:917px;left:601px;width:240px;height:169px;background:linear-gradient(135deg,#3a2e26,#a8876b 50%,#5a4536)}
.t4{top:917px;left:845px;width:241px;height:169px;background:linear-gradient(90deg,#7a5b46,#4a3426 55%,#231a14)}
.party{position:absolute;left:52px;top:15px;width:136px;height:136px;border-radius:50%;background:var(--white);text-align:center;padding-top:30px}
.party .s{font-family:"Playfair Display",serif;font-style:italic;font-size:20px;color:var(--salmon);line-height:22px}
.party .p{font-family:"Oswald",sans-serif;font-weight:300;font-size:36px;color:#555;line-height:40px}
.party .c{font-size:9px;font-weight:600;color:#555}
.sellers{position:absolute;left:25px;top:124px;font-family:"Oswald",sans-serif;font-weight:300;font-size:28px;color:var(--white)}
.leather{position:absolute;left:18px;top:42px;font-family:"Oswald",sans-serif;font-size:34px;line-height:36px;color:var(--white)}
.btn-blue{position:absolute;left:32px;top:124px;width:96px;height:26px;background:var(--blue);color:var(--white);font-size:10px;font-weight:600;line-height:26px;text-align:center}
.tabs{top:1136px;left:114px;display:flex;font-size:14px;color:#444}
.tabs span{height:47px;line-height:47px;padding:0 21px;white-space:nowrap}
.tabs .on{background:var(--salmon);color:var(--white)}
.tab-arrow{top:1136px;width:47px;height:47px;background:#efefef}
.tab-arrow.next{background:var(--salmon)}
.tab-arrow svg{position:absolute;top:15px;left:16px}
.hotband{top:1183px;left:0;width:1200px;height:455px;background:var(--salmon);overflow:hidden}
.card{position:absolute;width:222px;height:394px;background:var(--white);text-align:center}
.card-photo{position:relative;height:290px}
.card-name{font-size:11px;font-weight:600;color:#333;margin-top:14px;text-transform:uppercase;white-space:nowrap}
.card-price{font-size:23px;color:#333;line-height:30px;margin-top:2px}
.btn-cart{display:inline-block;margin-top:8px;width:120px;height:30px;background:var(--coral-btn);color:var(--white);font-size:11px;line-height:30px;box-shadow:0 3px 0 #c8493a;white-space:nowrap}
.sale{position:absolute;top:0;left:0}
.card.feature{width:240px;height:417px;box-shadow:0 4px 14px rgba(0,0,0,.25)}
.card.feature .card-photo{height:302px}
.shop-it{position:absolute;left:57px;top:100px;width:126px;height:126px;border-radius:50%;background:rgba(30,30,30,.85);color:var(--white);font-size:12px;padding-top:70px}
.shop-it i{position:absolute;left:52px;top:38px;width:22px;height:22px;background:var(--white);border-radius:3px}
.studio-dark{background:radial-gradient(ellipse 28% 45% at 50% 58%,#2b2b2b 0%,#555 55%,rgba(200,200,200,0) 100%),linear-gradient(180deg,#e6e6e6,#c9c9c9)}
.studio-light{background:radial-gradient(ellipse 28% 45% at 50% 58%,#f7f7f7 0%,#e5e5e5 60%,rgba(210,210,210,0) 100%),linear-gradient(180deg,#eeeeee,#d2d2d2)}
.rule{height:1px;background:var(--line)}
.clearance{top:1664px;left:523px;width:154px;height:154px}
.brands-title{top:2294px;left:0;width:1200px;text-align:center;font-size:14px;font-weight:700;letter-spacing:1px;color:#222}
.brands{top:2342px;left:114px;width:972px;display:flex;justify-content:space-between;align-items:center;font-family:"Oswald",sans-serif;font-weight:500;font-size:18px;color:#111;white-space:nowrap}
.about{top:2430px;left:114px;width:972px;text-align:center}
.about h2{font-weight:400;font-size:24px;color:#222;margin-bottom:12px}
.about p{font-size:12px;line-height:18px;color:#999}
.payband{top:2570px;left:0;width:1200px;height:54px;background:var(--band)}
.payband .t{position:absolute;left:319px;top:19px;font-size:11px;color:#999}
.pay{position:absolute;top:16px;width:34px;height:22px;background:var(--white);border:1px solid #ccc}
.footer{top:2624px;left:0;width:1200px;height:201px;background:var(--footer)}
.fcol{position:absolute;top:38px;font-size:11px;line-height:18px;color:#666;white-space:nowrap}
.fcol h4{font-size:14px;color:#222;margin-bottom:8px;font-weight:700}
.fsoc{display:grid;grid-template-columns:repeat(3,33px);gap:11px}
.fsoc i{width:33px;height:33px;border-radius:50%;background:#555}
.secure{position:absolute;left:968px;top:40px}
.bottombar{top:2825px;left:0;width:1200px;height:74px;background:#141414;font-size:10px;color:#aaa}
.bottombar .links{position:absolute;left:114px;top:30px;display:flex;gap:14px}
.bottombar .links .on{color:var(--red)}
.bottombar .copy{position:absolute;right:114px;top:24px;text-align:right;line-height:15px}
</style>
</head>
<body>

<header>
  <div class="abs topbar">
    <span style="left:114px">CUSTOM CARE: &nbsp;555-01-2390</span>
    <span style="left:728px">$ US ▾</span>
    <i class="abs sep" style="left:788px"></i>
    <span style="left:806px">LOGIN / REGISTER</span>
    <i class="abs sep" style="left:912px"></i>
    <span style="left:962px">MY ACCOUNT</span>
    <i class="abs sep" style="left:1045px"></i>
    <svg class="abs" style="left:1058px;top:7px" width="15" height="15" viewBox="0 0 15 15"><circle cx="6" cy="6" r="4.5" fill="none" stroke="#fff" stroke-width="2"/><line x1="9.5" y1="9.5" x2="14" y2="14" stroke="#fff" stroke-width="2"/></svg>
  </div>
  <div class="abs logo">
    <div class="logo-mark"></div>
    <div class="logo-name">ORV GROUP<br>ORBEL VANTRA</div>
  </div>
  <nav class="abs nav">
    <span>Online Shopping</span><span>About Us</span><span>Designer</span><span>News</span><span>Member Center</span>
  </nav>
  <div class="abs cart">
    <span class="label">Your cart</span>
    <i class="bag"></i>
    <span class="total">0 ITEMS &nbsp;| &nbsp;$ 0</span>
  </div>
</header>

<section class="abs hero">
  <div class="hero-photo" role="img" aria-label="Model in a coral top and denim shorts from the summer collection"></div>
</section>
<div class="abs hero-rule"></div>
<div class="abs hero-copy">
  <div class="hero-kicker"><i></i>Crazy<i></i></div>
  <div class="hero-title">CRAZY<br>SUMMER</div>
  <div class="hero-bar"></div><div class="hero-bar thin"></div>
  <div class="hero-sub">WOMAN COLLECTION</div>
</div>
<div class="abs btn-hero">SHOP NOW &nbsp;▸</div>
<div class="abs slide-arrow" style="left:0"><svg width="12" height="16"><path d="M9 2 3 8l6 6" fill="none" stroke="#999" stroke-width="2"/></svg></div>
<div class="abs slide-arrow" style="left:1170px"><svg width="12" height="16"><path d="M3 2l6 6-6 6" fill="none" stroke="#999" stroke-width="2"/></svg></div>
<div class="abs dots"><i></i><i class="on"></i><i></i><i></i><i></i></div>

<section class="abs newsband">
  <span class="t" style="left:114px">Stay updated</span>
  <div class="email">Your email address</div>
  <div class="email-go"><svg width="29" height="29"><path d="M14.5 9v11M9 14.5h11" stroke="#fff" stroke-width="2"/></svg></div>
  <span class="t" style="left:838px">Find us here</span>
  <div class="social-tab" style="left:920px"><i></i></div>
  <div class="social-tab" style="left:975px"><i></i></div>
  <div class="social-tab" style="left:1030px;border-right:1px solid #d4d4d4"><i></i></div>
</section>

<section class="promo">
  <div class="tile tile-main" role="img" aria-label="Man in a dark blazer and white shirt">
    <div class="looks"><div class="a">BEST</div><div class="b">OUTFITS</div><span class="c">&amp;</span><div class="d">LOOKS</div></div>
  </div>
  <div class="tile t1" role="img" aria-label="Model in a blue printed top"></div>
  <div class="tile t2" role="img" aria-label="Blue party backdrop">
    <div class="party"><div class="s">Summer</div><div class="p">PARTY</div><div class="c">COLLECTION</div></div>
  </div>
  <div class="tile t3" role="img" aria-label="Woman in white sunglasses"><div class="sellers">BEST SELLERS</div></div>
  <div class="tile t4" role="img" aria-label="Man in a leather jacket"><div class="leather">FALL<br>LEATHER</div><div class="btn-blue">SHOP NOW ▸</div></div>
</section>

<div class="abs tabs"><span class="on">WHAT'S HOT?</span><span>DESIGNERS</span><span>FEATURED</span><span>LATEST</span></div>
<div class="abs tab-arrow" style="left:992px"><svg width="14" height="18"><path d="M10 2 3 9l7 7" fill="none" stroke="#bbb" stroke-width="2"/></svg></div>
<div class="abs tab-arrow next" style="left:1039px"><svg width="14" height="18"><path d="M4 2l7 7-7 7" fill="none" stroke="#fff" stroke-width="2"/></svg></div>

<section class="abs hotband">
  <div class="card" style="left:-137px;top:30px"><div class="card-photo" role="img" aria-label="Model in a blue top" style="background:linear-gradient(135deg,#5fb6dc,#2a7fae)"></div><div class="card-name">Print Top</div><div class="card-price">$39.95</div><span class="btn-cart">ADD TO CART ✚</span></div>
  <div class="card" style="left:114px;top:30px"><div class="card-photo studio-dark" role="img" aria-label="Model in a white top and black wrap skirt"></div><div class="card-name">Mimosa Lace Dress</div><div class="card-price">$76.95</div><span class="btn-cart">ADD TO CART ✚</span></div>
  <div class="card" style="left:365px;top:30px"><div class="card-photo studio-light" role="img" aria-label="Model in a white skirt and jacket"><svg class="sale" width="50" height="50"><polygon points="0,0 50,0 0,50" fill="#222"/><text x="5" y="15" font-size="9" fill="#fff" font-family="Open Sans,sans-serif">SALE</text></svg></div><div class="card-name">Feel Tank</div><div class="card-price">$59.95</div><span class="btn-cart">ADD TO CART ✚</span></div>
  <div class="card feature" style="left:605px;top:19px"><div class="card-photo studio-dark" role="img" aria-label="Man in a printed shirt and white shorts"><div class="shop-it"><i></i>SHOP IT</div></div><div class="card-name">Hot Shorts</div><div class="card-price">$35.95</div><span class="btn-cart">ADD TO CART ✚</span></div>
  <div class="card" style="left:864px;top:30px"><div class="card-photo" role="img" aria-label="Model in a blue printed dress" style="background:linear-gradient(135deg,#78c3e6,#2b8fc4)"><svg class="sale" width="50" height="50"><polygon points="0,0 50,0 0,50" fill="#222"/><text x="5" y="15" font-size="9" fill="#fff" font-family="Open Sans,sans-serif">SALE</text></svg></div><div class="card-name">Mimosa Lace Dress</div><div class="card-price">$76</div><span class="btn-cart">ADD TO CART ✚</span></div>
  <div class="card" style="left:1115px;top:30px"><div class="card-photo" role="img" aria-label="Model in a yellow outfit" style="background:linear-gradient(135deg,#f4f1e6,#e8e26a)"><svg class="sale" width="50" height="50"><polygon points="0,0 50,0 0,50" fill="#222"/><text x="5" y="15" font-size="9" fill="#fff" font-family="Open Sans,sans-serif">SALE</text></svg></div><div class="card-name">Nice Top</div><div class="card-price">$29.95</div><span class="btn-cart">ADD TO CART ✚</span></div>
</section>

<div class="abs rule" style="top:1741px;left:114px;width:972px"></div>
<svg class="abs clearance" viewBox="0 0 154 154">
  <circle cx="77" cy="77" r="72" fill="#fff"/>
  <circle cx="77" cy="77" r="71" fill="none" stroke="#3b3b3b" stroke-width="10" stroke-dasharray="5.5 3.8"/>
  <circle cx="77" cy="77" r="67" fill="#3b3b3b"/>
  <circle cx="77" cy="77" r="58" fill="none" stroke="#fff" stroke-width="1.5" stroke-dasharray="3 3"/>
  <text x="77" y="63" text-anchor="middle" font-family="Oswald,sans-serif" font-size="17" fill="#fff">CLEARANCE</text>
  <text x="68" y="107" text-anchor="middle" font-family="Oswald,sans-serif" font-size="44" fill="#fff">50</text>
  <text x="104" y="88" text-anchor="middle" font-family="Oswald,sans-serif" font-size="14" fill="#fff">%</text>
  <text x="104" y="104" text-anchor="middle" font-family="Oswald,sans-serif" font-size="12" fill="#fff">OFF</text>
</svg>

<section class="clear-grid">
  <div class="card" style="left:114px;top:1843px;background:#f3f3f3"><div class="card-photo studio-dark" role="img" aria-label="Model in a white top and black wrap skirt"></div><div class="card-name">Nadia Dress</div><div class="card-price">$64.95</div><span class="btn-cart">ADD TO CART ✚</span></div>
  <div class="card" style="left:365px;top:1843px;background:#f3f3f3"><div class="card-photo" role="img" aria-label="Model in a white blouse and printed shorts" style="background:radial-gradient(ellipse 28% 45% at 50% 55%,#faf8f5 0%,#e8ddd2 60%,rgba(220,211,201,0) 100%),linear-gradient(180deg,#f1ede8,#dcd3c9)"><svg class="sale" width="50" height="50"><polygon points="0,0 50,0 0,50" fill="#222"/><text x="5" y="15" font-size="9" fill="#fff" font-family="Open Sans,sans-serif">SALE</text></svg></div><div class="card-name">Sofi Blouse</div><div class="card-price">$26.95</div><span class="btn-cart">ADD TO CART ✚</span></div>
  <div class="card" style="left:614px;top:1843px;background:#f3f3f3"><div class="card-photo studio-dark" role="img" aria-label="Man in a printed shirt and white shorts"></div><div class="card-name">Gooding Shorts</div><div class="card-price">$79.95</div><span class="btn-cart">ADD TO CART ✚</span></div>
  <div class="card" style="left:864px;top:1843px;background:#f3f3f3"><div class="card-photo" role="img" aria-label="Model in a sheer tank and black shorts" style="background:radial-gradient(ellipse 28% 45% at 50% 60%,#5a504a 0%,#a89a90 55%,rgba(207,194,184,0) 100%),linear-gradient(180deg,#efe9e4,#cfc2b8)"><svg class="sale" width="50" height="50"><polygon points="0,0 50,0 0,50" fill="#222"/><text x="5" y="15" font-size="9" fill="#fff" font-family="Open Sans,sans-serif">SALE</text></svg></div><div class="card-name">Mimosa Lace Dress</div><div class="card-price">$76</div><span class="btn-cart">ADD TO CART ✚</span></div>
</section>

<div class="abs rule" style="top:2303px;left:0;width:1200px"></div>
<div class="abs brands-title"><span style="background:#fff;padding:0 24px">FAVOURITE BRANDS</span></div>
<div class="abs brands"><span>NORVEN</span><span>HALBERT SHIP</span><span>KESTRA</span><span>GIRL MADRID</span><span>TRAVERSO</span><span>LORNE VICKERY</span><span>MARLOW</span><span>BRISKEN</span></div>
<div class="abs rule" style="top:2405px;left:0;width:1200px"></div>

<section class="abs about">
  <h2>About Orbel Vantra</h2>
  <p>This is Pixelwork's version of Lorem Ipsum. Proin gravida nibh vel velit auctor aliquet. Aenean sollicitudin, lorem quis bibendum auctor, nisi elit consequat ipsum, nec sagittis sem nibh id elit. Duis sed odio sit amet nibh vulputate cursus a sit amet mauris. Morbi accumsan ipsum velit. Nam nec tellus a odio tincidunt auctor a ornare odio. Sed non mauris vitae erat consequat auctor eu in elit. Class aptent taciti sociosqu ad litora torquent per conubia nostra, per inceptos himenaeos. Mauris in erat justo. Nullam ac urna eu felis dapibus condimentum sit amet a augue.</p>
</section>

<section class="abs payband">
  <span class="t">We accept</span>
  <i class="pay" style="left:390px"></i><i class="pay" style="left:432px"></i><i class="pay" style="left:474px"></i><i class="pay" style="left:516px"></i><i class="pay" style="left:558px"></i><i class="pay" style="left:600px"></i><i class="pay" style="left:642px"></i><i class="pay" style="left:684px"></i><i class="pay" style="left:726px"></i><i class="pay" style="left:768px"></i><i class="pay" style="left:810px"></i><i class="pay" style="left:852px;background:#e23b36;border-color:#e23b36"></i>
</section>

<footer class="abs footer">
  <div class="fcol" style="left:114px"><h4>Customer Service</h4>Contact<br>FAQ<br>Terms of payment<br>Terms of sale<br>Delivery terms and conditions<br>Returns and Refunds</div>
  <div class="fcol" style="left:317px"><h4>Information</h4>Affiliate<br>Cookies<br>How to Shop<br>About Owner<br>Investor relations</div>
  <div class="fcol" style="left:479px"><h4>Campaigns</h4>Evening dresses<br>Makeup<br>Fashion forward<br>training clothes<br>Special Occasion Dresses</div>
  <div class="fcol" style="left:672px"><h4>Stores</h4>Beijing<br>New York<br>London<br>Hong Cong<br>Tokio</div>
  <div class="fcol" style="left:788px"><h4>Social</h4><div class="fsoc"><i></i><i></i><i></i><i></i><i></i><i></i></div></div>
  <svg class="secure" width="122" height="122" viewBox="0 0 122 122"><circle cx="61" cy="61" r="58" fill="#d9d9d9"/><circle cx="61" cy="61" r="46" fill="none" stroke="#fff" stroke-width="3"/></svg>
</footer>

<div class="abs bottombar">
  <div class="links"><span class="on">Home</span><span>|</span><span>Online</span><span>|</span><span>Shopping</span><span>|</span><span>About Us</span><span>|</span><span>Designer</span><span>|</span><span>News</span><span>|</span><span>Member Center</span></div>
  <div class="copy">© Orbel Vantra<br>All Rights Reserved</div>
</div>

</body>
</html>
```